Northvale Strategy Partners Website Design

I need a website design for my new business consulting and executive coaching firm, Northvale Strategy Partners. We provide consultative services to business C-suites as well as personal coaching to executives. I have attached the logo with color scheme I have chosen. I would like the website to reflect professionalism and continue the color scheme in the logo.

Target Market(s)

Small to medium business and their executives; middle to upper income men and women in mid- to late career looking for significance

Industry/Entity Type

Business Consultant

Number of Pages Required

4 page

Requirements
Must have
• A homepage with prominent logo and way to contact for more information; an area on the homepage with easy to read, clear text to describe what the company does; a prominent area on the homepage for a tagline; a blog page that can be updated regularly, an "about us" page with biographical information; an "about us" page; a page detailing services offered
• The web design must match the logo colors and font that I have uploaded.
Nice to have
• A lighthouse picture in the background or header
Should not have
• A lot of text area on the homepage

```html
<!DOCTYPE html>
<html lang="en">
<head>
<meta charset="utf-8">
<title>Northvale Strategy Partners</title>
<link rel="stylesheet" href="https://fonts.googleapis.com/css2?family=Archivo+Black&family=Marcellus&family=Open+Sans:wght@400;600;700&display=swap">
<style>
:root{
  --navy:#1b2a5e;
  --wine:#6f0c10;
  --wine-dark:#5e0a0d;
  --ink:#333333;
  --muted:#555555;
  --paper:#ffffff;
  --mist:#e9e9e9;
  --line:#d6d6d6;
  --night:#0b0b0b;
}
*{margin:0;padding:0;box-sizing:border-box}
html,body{width:1200px;height:2752px;overflow:hidden}
body{position:relative;background:var(--paper);font-family:"Open Sans",Arial,sans-serif;color:var(--ink)}
.abs{position:absolute}
.heading{font-family:"Archivo Black","Arial Black",sans-serif;font-size:33px;letter-spacing:1px;color:var(--navy);text-transform:uppercase;line-height:1;white-space:nowrap}
.heading em{font-style:normal;color:var(--wine)}
.center{left:0;width:1200px;text-align:center}

/* header */
.site-header{top:0;left:0;width:1200px;height:130px;background:var(--paper)}
.brand{display:flex;align-items:center;gap:10px;font-family:"Marcellus",serif;color:var(--navy)}
.brand-square{width:14px;height:14px;background:var(--wine);flex:none}
.header-brand{left:73px;top:48px;font-size:21px;width:220px;line-height:1.2}
.main-nav a{position:absolute;top:0;height:130px;line-height:134px;font-size:15px;color:#222;text-decoration:none;text-transform:uppercase;white-space:nowrap}
.main-nav a.active{background:var(--wine);color:#fff;text-align:center;width:104px;left:481px}

/* hero */
.hero{top:130px;left:0;width:1200px;height:521px;background:linear-gradient(180deg,#1d2738 0%,#2c3444 45%,#3a3a36 75%,#2a2720 100%)}
.hero-lighthouse{left:175px;top:150px;width:120px;height:371px;background:linear-gradient(180deg,#6b6d72,#8a5850 50%,#5a4b44)}
.hero-person{left:899px;top:0;width:301px;height:521px;background:linear-gradient(180deg,#6d5347,#b9c5d6 55%,#c9d2df)}
.hero-title{left:303px;top:162px;width:596px;border-top:1px solid rgba(255,255,255,.8);border-bottom:1px solid rgba(255,255,255,.8);padding:9px 0;text-align:center;font-family:"Archivo Black","Arial Black",sans-serif;font-weight:400;color:#fff;font-size:28px;line-height:34px;letter-spacing:.5px;white-space:nowrap}
.hero-text{left:290px;top:226px;width:622px;text-align:center;color:#fff;font-size:16px;font-weight:600;line-height:22px}
.circle-btn{width:62px;height:62px;border-radius:50%;border:2px solid rgba(255,255,255,.85);color:#fff;font-size:30px;line-height:54px;text-align:center;font-weight:700}
.circle-btn.filled{background:var(--wine)}

/* about */
.about-brand{left:110px;top:826px;width:240px;font-size:30px;line-height:1.15;flex-direction:column;align-items:center;text-align:center}
.about-divider{left:391px;top:697px;width:1px;height:288px;background:var(--line)}
.about-rule{left:391px;top:791px;width:679px;height:1px;background:var(--line)}
.about-text{left:435px;top:822px;width:640px;font-size:17px;line-height:29px;color:var(--muted)}

/* services */
.services{top:1037px;left:0;width:1200px;height:437px;background:linear-gradient(90deg,#1f1f1f,#3a3a3a 45%,#2a2a2a 70%,#3c3f3a)}
.services-title{color:#fff;top:1100px;font-family:"Archivo Black","Arial Black",sans-serif;font-size:31px;letter-spacing:1px}
.service{width:420px;text-align:center;color:#fff}
.service h3{font-family:"Marcellus",serif;font-weight:400;font-size:26px;margin-top:16px}
.service p{font-size:15px;line-height:24px;margin-top:10px}
.services-divider{left:600px;top:1174px;height:239px;border-left:2px dashed rgba(255,255,255,.7)}

/* subscribe */
.subscribe{top:1474px;left:0;width:1200px;height:156px;background:var(--mist)}
.subscribe-input{left:125px;top:1529px;width:638px;height:55px;border:1px solid #bdbdbd;background:#ececec;font-family:"Marcellus",serif;font-size:18px;color:#777;line-height:53px;padding-left:20px}
.subscribe-btn{left:771px;top:1529px;width:207px;height:55px;background:var(--wine);color:#fff;font-family:"Marcellus",serif;font-size:18px;display:flex;align-items:center;justify-content:center;gap:16px}

/* testimonials */
.quote{width:312px}
.quote-mark{font-family:"Archivo Black",sans-serif;font-size:90px;color:#d3d3d3;line-height:60px;height:40px;overflow:hidden}
.quote p{font-size:15px;line-height:23px;color:var(--ink);margin-top:-22px;position:relative}
.quote .name{font-family:"Marcellus",serif;font-size:19px;color:var(--wine);margin-top:14px}
.quote .role{font-size:14px;color:var(--wine);margin-top:2px}
.circle-btn.dark{border-color:#555;color:#333}

/* blog */
.blog{top:2042px;left:0;width:1200px;height:334px;background:var(--mist)}
.blog-text{left:210px;top:2170px;width:780px;text-align:center;font-size:15px;line-height:27px;color:var(--ink)}
.read-more{top:2236px;font-weight:700;font-size:16px;color:var(--wine);text-decoration:underline}
.blog-meta{top:2294px;display:flex;justify-content:center;gap:40px;font-family:"Marcellus",serif;font-size:13px;color:#555}
.blog-meta span{display:flex;align-items:center;gap:10px}

/* footer */
.footer{top:2376px;left:0;width:1200px;height:312px;background:var(--wine)}
.footer-title{font-family:"Marcellus",serif;font-weight:400;font-size:19px;color:#fff;text-transform:uppercase}
.contact-item{left:79px;display:flex;gap:18px;color:#fff;font-size:15px;line-height:23px}
.contact-item svg{flex:none;margin-top:2px}
.footer-brand{left:480px;top:2470px;width:240px;font-size:26px;color:#fff;flex-direction:column;text-align:center;line-height:1.15}
.footer-brand .brand-square{background:#fff}
.social{width:36px;height:36px;border-radius:50%;border:1px solid rgba(255,255,255,.5);background:var(--wine-dark)}
.social.first{background:#fff}
.footer-nav{left:912px;top:2458px;width:211px;list-style:none}
.footer-nav li{height:40px;border-bottom:1px solid rgba(255,255,255,.85);color:#fff;font-family:"Marcellus",serif;font-size:17px;line-height:38px;padding-left:30px;position:relative}
.footer-nav li::before{content:"";position:absolute;left:6px;top:14px;border-left:7px solid #e0262d;border-top:5px solid transparent;border-bottom:5px solid transparent}
.footer-nav li:last-child{border-bottom:none}
.copyright{top:2688px;left:0;width:1200px;height:64px;background:var(--night);color:#ddd;font-size:12px;text-align:center;line-height:64px}
.copyright em{font-style:normal;color:#c21a20}
</style>
</head>
<body>

<header class="site-header abs">
  <div class="brand header-brand abs"><span class="brand-square"></span><span>Northvale Strategy Partners</span></div>
  <nav class="main-nav">
    <a class="active" href="#">Home</a>
    <a href="#" style="left:596px">About Us</a>
    <a href="#" style="left:714px">Services</a>
    <a href="#" style="left:817px">Testimonial</a>
    <a href="#" style="left:952px">Blog</a>
    <a href="#" style="left:1033px">Contact Us</a>
  </nav>
</header>

<section class="hero abs" role="img" aria-label="Lighthouse under a stormy evening sky">
  <div class="hero-lighthouse abs" role="img" aria-label="Red and white lighthouse tower"></div>
  <div class="hero-person abs" role="img" aria-label="Smiling professional woman with arms crossed"></div>
  <h1 class="hero-title abs">LOREM IPSUME DOLOR SIT AMET</h1>
  <p class="hero-text abs">Lorem ipsum dolor sit amet, consectetur adipiscing elit, sed do eiusmod tempor<br>incididunt ut labore et dolore magna aliqua.</p>
  <div class="circle-btn filled abs" style="left:532px;top:289px">&laquo;</div>
  <div class="circle-btn abs" style="left:605px;top:289px">&raquo;</div>
</section>

<section class="about">
  <div class="brand about-brand abs"><span class="brand-square"></span><span>Northvale Strategy Partners</span></div>
  <div class="about-divider abs"></div>
  <h2 class="heading abs" style="left:435px;top:729px">Know <em>About Us</em></h2>
  <div class="about-rule abs"></div>
  <p class="about-text abs">Lorem ipsum dolor sit amet, consectetur adipiscing elit, sed do eiusmod tempor incididunt ut labore et dolore magna aliqua. Ut enim ad minim veniam, quis nostrud exercitation ullamco laboris nisi ut aliquip ex ea commodo consequat. Duis aute irure dolor in reprehenderit.</p>
</section>

<section class="services abs" role="img" aria-label="Business team meeting in an office"></section>
<h2 class="services-title abs center">WHAT WE DO</h2>
<div class="services-divider abs"></div>
<div class="service abs" style="left:111px;top:1175px">
  <svg width="112" height="112" viewBox="0 0 112 112" fill="#fff">
    <circle cx="35" cy="50" r="13"/><path d="M12 100c0-18 10-28 23-28s23 10 23 28z"/>
    <circle cx="74" cy="22" r="13"/><path d="M51 72c0-18 10-28 23-28s23 10 23 28z"/>
    <path d="M24 30c2-12 12-18 24-18" stroke="#fff" stroke-width="4" fill="none"/><path d="M44 6l8 6-9 5z"/>
    <path d="M98 60c0 14-8 24-22 26" stroke="#fff" stroke-width="4" fill="none"/><path d="M80 92l-8-6 9-5z"/>
  </svg>
  <h3>Consultative Services</h3>
  <p>Lorem ipsum dolor sit amet, consectetur adipiscing<br>elit, sed do eiusmod tempor incididunt.</p>
</div>
<div class="service abs" style="left:671px;top:1175px">
  <svg width="112" height="112" viewBox="0 0 112 112" fill="#fff">
    <circle cx="40" cy="40" r="18"/><path d="M8 100c0-26 14-38 32-38s32 12 32 38z"/>
    <circle cx="74" cy="40" r="18"/><path d="M44 100c0-26 14-38 30-38s30 12 30 38z"/>
    <path d="M72 64l4 8-4 20-4-20z" fill="#333"/>
  </svg>
  <h3>Executive Coaching</h3>
  <p>Lorem ipsum dolor sit amet, consectetur adipiscing<br>elit, sed do eiusmod tempor incididunt.</p>
</div>

<section class="subscribe abs"></section>
<div class="subscribe-input abs">SUBSCRIBE HERE | EMAIL ID</div>
<div class="subscribe-btn abs">SEND
  <svg width="20" height="20" viewBox="0 0 20 20" fill="#fff"><path d="M19 1L1 9l6 2 2 7 3-5 5 3z"/></svg>
</div>

<h2 class="heading abs center" style="top:1682px">What Our <em>Client Say</em></h2>
<div class="quote abs" style="left:79px;top:1760px">
  <div class="quote-mark">&ldquo;</div>
  <p>Lorem ipsum dolor sit amet, consectetur adipiscing elit, sed do eiusmod tempor incididunt ut labore et dolore magna aliqua.</p>
  <div class="name">-Name Here</div><div class="role">Designation here</div>
</div>
<div class="quote abs" style="left:459px;top:1760px">
  <div class="quote-mark">&ldquo;</div>
  <p>Lorem ipsum dolor sit amet, consectetur adipiscing elit, sed do eiusmod tempor incididunt ut labore et dolore magna aliqua.</p>
  <div class="name">-Name Here</div><div class="role">Designation here</div>
</div>
<div class="quote abs" style="left:835px;top:1760px">
  <div class="quote-mark">&ldquo;</div>
  <p>Lorem ipsum dolor sit amet, consectetur adipiscing elit, sed do eiusmod tempor incididunt ut labore et dolore magna aliqua.</p>
  <div class="name">-Name Here</div><div class="role">Designation here</div>
</div>
<div class="circle-btn dark abs" style="left:542px;top:1943px;width:54px;height:54px;line-height:46px;font-size:26px">&laquo;</div>
<div class="circle-btn dark abs" style="left:604px;top:1943px;width:54px;height:54px;line-height:46px;font-size:26px">&raquo;</div>

<section class="blog abs"></section>
<h2 class="heading abs center" style="top:2100px">Our Latest <em>Blog</em></h2>
<p class="blog-text abs"><strong>Lorem ipsum dolor sit amet</strong>, consectetur adipiscing elit, sed do eiusmod tempor incididunt ut labore et dolore magna aliqua. Ut enim ad minim veniam, quis nostrud exercitation ullamco labori</p>
<div class="read-more abs center">READ MORE</div>
<div class="blog-meta abs center">
  <span><svg width="18" height="18" viewBox="0 0 18 18" fill="none" stroke="#8a1015" stroke-width="2"><rect x="2" y="3" width="14" height="13"/><path d="M2 7h14M6 1v4M12 1v4"/></svg>29-12-2015</span>
  <span><svg width="20" height="18" viewBox="0 0 20 18" fill="none" stroke="#8a1015" stroke-width="2"><ellipse cx="10" cy="8" rx="8" ry="6"/><path d="M5 13l-2 4 5-3"/></svg>20-Comment</span>
  <span><svg width="20" height="14" viewBox="0 0 20 14" fill="#8a1015"><path d="M10 1C5 1 1 7 1 7s4 6 9 6 9-6 9-6-4-6-9-6z"/><circle cx="10" cy="7" r="3" fill="#fff"/></svg>20 - View</span>
</div>

<footer class="footer abs"></footer>
<h4 class="footer-title abs" style="left:79px;top:2423px">Keep in Touch</h4>
<div class="contact-item abs" style="top:2490px">
  <svg width="20" height="18" viewBox="0 0 20 18" fill="#fff"><path d="M10 1L1 9h3v8h5v-5h2v5h5V9h3z"/></svg>
  <span>Lorem ipsum dolor sit amet,<br>consectetur adipiscing elit, sed do.</span>
</div>
<div class="contact-item abs" style="top:2556px">
  <svg width="20" height="20" viewBox="0 0 20 20" fill="#fff"><path d="M4 1l4 4-2 3c1 3 3 5 6 6l3-2 4 4-3 3C8 19 1 12 1 4z"/></svg>
  <span>+1 555 014 2290</span>
</div>
<div class="contact-item abs" style="top:2602px">
  <svg width="20" height="16" viewBox="0 0 20 16" fill="#fff"><rect x="1" y="2" width="18" height="13"/><path d="M1 2l9 7 9-7" stroke="#6f0c10" stroke-width="2" fill="none"/></svg>
  <span>hello@northvale.example</span>
</div>
<div class="brand footer-brand abs"><span class="brand-square"></span><span>Northvale Strategy Partners</span></div>
<div class="social first abs" style="left:518px;top:2569px"></div>
<div class="social abs" style="left:560px;top:2569px"></div>
<div class="social abs" style="left:602px;top:2569px"></div>
<div class="social abs" style="left:644px;top:2569px"></div>
<h4 class="footer-title abs" style="left:912px;top:2423px">Navigation</h4>
<ul class="footer-nav abs">
  <li>Home</li><li>About Us</li><li>Services</li><li>Blog</li><li>Contact Us</li>
</ul>
<div class="copyright abs">&copy; <em>NORTHVALE STRATEGY PARTNERS</em> - 2015. All Rights Reserved</div>

</body>
</html>
```